Professional and creative business card design for recruiting service providers

Our company supports German medium-sized companies in filling vacancies promptly. For this we use social media marketing and bring our customers into the visibility.

We want a professional but also creative design for our business cards.

Please look at lindqvar-staff.de to get an impression of our CI.

Target Market(s)

Small and medium-sized companies in Germany from the industry

Industry/Entity Type

Industrie, Handwerk

Contact Information for Business Card

Name, Position, Telefonnummer, Email, Website

Colors
EE7325
F08F49
F5BC92
FAE3D3
FDF4ED

Requirements
Must have
• A picture of the employee and in the style of www.lindqvar-staff.de

```html
<!DOCTYPE html>
<html lang="de">
<head>
<meta charset="utf-8">
<title>Lindqvar &amp; Staff – Visitenkarte</title>
<link href="https://fonts.googleapis.com/css2?family=Montserrat:wght@400;500;700&display=swap" rel="stylesheet">
<style>
  :root {
    --orange: #EE7325;
    --orange-deep: #F05F30;
    --ink: #1f1f1f;
    --paper: #ffffff;
    --card-dark: #262626;
    --stage: #2a2a2a;
    --suit-top: #3a3d47;
    --suit-bottom: #1b1c22;
  }
  * { margin: 0; padding: 0; box-sizing: border-box; }
  html, body {
    width: 1200px; height: 1059px; overflow: hidden;
    background: var(--stage);
    font-family: "Montserrat", sans-serif;
  }
  .canvas { position: relative; width: 1200px; height: 1059px; }

  .card {
    position: absolute;
    width: 688px; height: 392px;
    border-radius: 22px;
    overflow: hidden;
  }

  /* Front */
  .card-front { left: 257px; top: 89px; background: var(--paper); }
  .brand {
    position: absolute; left: 33px; top: 66px;
    display: flex; align-items: center; gap: 16px;
  }
  .brand-square { width: 60px; height: 60px; background: var(--orange-deep); }
  .brand-name {
    font-weight: 700; font-size: 24px; line-height: 27px;
    letter-spacing: 1.6px; color: var(--ink); text-transform: uppercase;
  }
  .name-band {
    position: absolute; left: 0; top: 188px; width: 100%; height: 58px;
    background: var(--orange-deep);
    padding: 8px 0 0 34px; color: var(--paper);
  }
  .person-name { font-weight: 700; font-size: 21px; letter-spacing: 0.6px; line-height: 24px; }
  .person-role { font-weight: 500; font-size: 15px; line-height: 20px; }
  .contacts {
    position: absolute; left: 33px; top: 274px; list-style: none;
    color: var(--ink); font-size: 16px; letter-spacing: 0.3px;
  }
  .contacts li { display: flex; align-items: center; gap: 6px; height: 29.5px; }
  .contacts svg { width: 12px; height: 12px; fill: var(--orange-deep); flex: none; }
  .portrait {
    position: absolute; left: 336px; top: 36px; width: 352px; height: 356px;
    background: linear-gradient(180deg, rgba(200,160,130,0.9) 0%, #c59a7c 22%, var(--suit-top) 45%, var(--suit-bottom) 100%);
    border-radius: 120px 120px 0 0;
  }

  /* Back */
  .card-back { left: 254px; top: 547px; background: var(--card-dark); }
  .back-mark {
    position: absolute; left: 38px; top: 42px; width: 278px; height: 278px;
    background: #1c1c1c;
  }
  .back-name {
    position: absolute; right: 36px; top: 252px; text-align: left;
    color: var(--paper); font-weight: 700; font-size: 46px; line-height: 50px;
    letter-spacing: 3px; text-transform: uppercase;
  }
</style>
</head>
<body>
<main class="canvas">

  <section class="card card-front" aria-label="Visitenkarte Vorderseite">
    <div class="brand">
      <span class="brand-square"></span>
      <span class="brand-name">Lindqvar<br>&amp; Staff</span>
    </div>

    <div class="name-band">
      <p class="person-name">JONAS LINDQVAR</p>
      <p class="person-role">Gründer</p>
    </div>

    <ul class="contacts">
      <li>
        <svg viewBox="0 0 24 24"><path d="M6.6 10.8a15.1 15.1 0 0 0 6.6 6.6l2.2-2.2c.3-.3.7-.4 1-.2 1.1.4 2.3.6 3.6.6.6 0 1 .4 1 1V20c0 .6-.4 1-1 1C10.6 21 3 13.4 3 4c0-.6.4-1 1-1h3.5c.6 0 1 .4 1 1 0 1.3.2 2.5.6 3.6.1.3 0 .7-.2 1z"/></svg>
        (123) 456 7890
      </li>
      <li>
        <svg viewBox="0 0 24 24"><path d="M2 5h20v2l-10 6L2 7zM2 9.3l10 6 10-6V19H2z"/></svg>
        info@lindqvar-staff.de
      </li>
      <li>
        <svg viewBox="0 0 24 24"><path d="M12 2a10 10 0 1 0 0 20 10 10 0 0 0 0-20zm6.9 6h-3a15 15 0 0 0-1.3-3.9A8 8 0 0 1 18.9 8zM12 4c.8 1.2 1.5 2.5 1.9 4h-3.8c.4-1.5 1.1-2.8 1.9-4zM4.3 14a8 8 0 0 1 0-4h3.4a16 16 0 0 0 0 4zm.8 2h3a15 15 0 0 0 1.3 3.9A8 8 0 0 1 5.1 16zm3-8h-3a8 8 0 0 1 4.3-3.9C8.8 5.3 8.4 6.6 8.1 8zM12 20c-.8-1.2-1.5-2.5-1.9-4h3.8c-.4 1.5-1.1 2.8-1.9 4zm2.3-6H9.7a14 14 0 0 1 0-4h4.6a14 14 0 0 1 0 4zm.3 5.9c.6-1.2 1-2.5 1.3-3.9h3a8 8 0 0 1-4.3 3.9zm1.7-5.9a16 16 0 0 0 0-4h3.4a8 8 0 0 1 0 4z"/></svg>
        www.lindqvar-staff.de
      </li>
    </ul>

    <div class="portrait" role="img" aria-label="Porträtfoto des Gründers in dunklem Sakko und Rollkragenpullover"></div>
  </section>

  <section class="card card-back" aria-label="Visitenkarte Rückseite">
    <span class="back-mark"></span>
    <p class="back-name">Lindqvar<br>&amp; Staff</p>
  </section>

</main>
</body>
</html>
```